Dental Co needs single page print ad

Dental company needs a 1 page ad for trade magazines.
I am uploading an example of what we want (words). We need you to make it look great. It can include people or not.
The uploaded ad isn't there to be copied, just to kind of frame what we are thinking. We are open to any design
One page ad
Size 1)

Trim Size - 8 x 10.5
Bleed Size - 8.25 x 10.75
Live Area - 7 x 10

Size 2)

Trim - 8 x 10.875
Bleed - 8.25 x 11.125
Live Area - 7 x 9.875

PLUM Brand Hex #'s

Orange - ff6319
Teal - 56b1bf
Lt. Teal - aed9da
Blue: #38394B

Target Market(s)

Dentists

Requirements
Must have
• PLUM Logo, pic of the sensor (called KITE)
Use the brand hex colors:
Orange - ff6319
Teal - 56b1bf
Lt. Teal - aed9da
Blue: #38394B

```html
<!DOCTYPE html>
<html lang="en">
<head>
<meta charset="utf-8">
<title>PLUM Imaging – KITE Sensor Subscription</title>
<link rel="stylesheet" href="https://fonts.googleapis.com/css2?family=Montserrat:wght@700;800;900&family=Courier+Prime&display=swap">
<style>
  :root {
    --orange: #ff6319;
    --teal: #56b1bf;
    --light-teal: #aed9da;
    --navy: #38394b;
  }
  * { margin: 0; padding: 0; box-sizing: border-box; }
  html, body { width: 914px; height: 1200px; overflow: hidden; }
  body { background: var(--orange); font-family: "Montserrat", Arial, sans-serif; }

  .ad { position: relative; width: 914px; height: 1200px; background: var(--orange); overflow: hidden; }

  .headline-box {
    position: absolute; left: 59px; top: 56px; width: 795px; height: 131px;
    border: 6px solid var(--light-teal);
    display: flex; align-items: center; padding-left: 26px;
  }
  .headline {
    color: var(--navy); font-weight: 900; font-size: 41px; line-height: 1.35;
    text-transform: uppercase; letter-spacing: 0.5px;
  }
  .footnote {
    position: absolute; right: 100px; top: 201px;
    font-family: "Courier Prime", "Courier New", monospace;
    font-size: 13px; letter-spacing: 1.5px; color: var(--navy);
  }

  .hero-circle {
    position: absolute; left: 172px; top: 236px; width: 566px; height: 566px;
    border-radius: 50%; background: var(--light-teal);
  }
  .sensor-visual { position: absolute; left: 0; top: 0; }

  .offer { position: absolute; left: 73px; top: 862px; color: var(--light-teal); }
  .offer-price { font-weight: 800; font-size: 27px; line-height: 37px; text-transform: uppercase; }
  .offer-perks { margin-top: 8px; list-style: none; font-weight: 700; font-size: 12.5px; line-height: 17px; text-transform: uppercase; }

  .contact-bar {
    position: absolute; left: -10px; top: 1079px; width: 653px; height: 62px;
    background: var(--light-teal); border: 3px solid var(--navy); border-radius: 0 12px 12px 0;
    display: flex; align-items: center; justify-content: center;
    font-family: "Courier Prime", "Courier New", monospace; font-size: 17px;
    letter-spacing: 3px; color: var(--navy);
  }
  .edge-tab {
    position: absolute; left: 877px; top: 1079px; width: 50px; height: 62px;
    background: var(--light-teal); border: 3px solid var(--navy); border-radius: 12px 0 0 12px;
  }
  .brand-name {
    position: absolute; left: 662px; top: 1064px; color: var(--navy);
    font-weight: 900; text-transform: uppercase; line-height: 0.95;
  }
  .brand-name .primary { display: block; font-size: 56px; letter-spacing: 1px; }
  .brand-name .secondary { display: block; font-size: 28px; letter-spacing: 1px; padding-left: 46px; }
</style>
</head>
<body>
  <main class="ad">
    <header class="headline-box">
      <h1 class="headline">A subscription option for<br>intra-oral sensor is dumb*</h1>
    </header>
    <p class="footnote">*UNTIL YOU DO THE MATH</p>

    <div class="hero-circle"></div>
    <svg class="sensor-visual" width="914" height="1200" viewBox="0 0 914 1200" role="img" aria-label="KITE intra-oral sensor product image with cable">
      <rect x="306" y="425" width="297" height="207" rx="34" fill="#3a3d55"/>
    </svg>

    <section class="offer">
      <p class="offer-price">$1,999 one-time sign up fee</p>
      <p class="offer-price">$139/mo - cancel anytime</p>
      <ul class="offer-perks">
        <li>Lifetime $0 deductible warranty</li>
        <li>Unlimited support &amp; upgrades</li>
        <li>Direct integration with all major software</li>
        <li>Affordable enough for every op</li>
        <li>Preserve your capital</li>
      </ul>
    </section>

    <footer>
      <div class="contact-bar">PLUMIMAGING.COM - (555) 234-PLUM</div>
      <div class="edge-tab"></div>
      <p class="brand-name"><span class="primary">Plum</span><span class="secondary">Imaging</span></p>
    </footer>
  </main>
</body>
</html>
```